Corinnehabbard.com

1. Conceptualization and designing of the site Homepage. The Homepage design will be completely customized and based on your design instructions (i.e. preferred colors, links to reference sites that you want us to take reference from if any etc) and the recently completed logo design.
2. Upon homepage design approval, based on it we will be creating the layout for the other 4 site inner pages (i.e. About page, Contact page, Services page, and Insights (publications, media).
3. Once all the inner page designs are approved, we will get the designs built (will make sure that the site is completely Responsive - works on all devices) within your provided WIX account.
4. We will add the static text and images provided by you to the Home page, About page, Contact page, and the Services page. For the 2 Insights sub-pages, we will add 1-2 sample Publications and Media entries.
once you confirm the total number of required entries for the 2 sub-pages, I will accordingly quote you on the same
5. Integration of a Contact form on the Contact page that will email the filled in details to your mail id.

```html
<!DOCTYPE html>
<html lang="en">
<head>
<meta charset="utf-8">
<title>Corinne Habbard Consulting</title>
<link href="https://fonts.googleapis.com/css2?family=Montserrat:wght@600;700;800&family=Open+Sans:wght@400;600;700&display=swap" rel="stylesheet">
<style>
:root{
  --blue:#1b8ed4;
  --orange:#f39200;
  --red:#d7261e;
  --green:#1a9a3c;
  --ink:#1d1d1d;
  --muted:#8a8a8a;
  --text:#555;
  --white:#fff;
}
html,body{margin:0;padding:0;overflow:hidden;background:var(--white);}
.page{position:relative;width:1200px;height:3691px;overflow:hidden;font-family:"Open Sans",sans-serif;color:var(--ink);}
.abs{position:absolute;}
.heading{font-family:"Montserrat",sans-serif;font-weight:700;color:var(--blue);font-size:44px;margin:0;letter-spacing:-0.5px;}
.btn{position:absolute;background:var(--orange);color:var(--white);font-family:"Montserrat",sans-serif;font-weight:700;font-size:13px;border-radius:24px;display:flex;align-items:center;justify-content:center;text-transform:uppercase;}
/* header */
.top-stripes{position:absolute;top:0;left:0;width:1200px;height:3px;display:flex;}
.top-stripes span{flex:1;}
.site-header{position:absolute;top:0;left:0;width:1200px;height:76px;background:var(--white);z-index:3;}
.brand-badge{position:absolute;left:138px;top:-90px;width:244px;height:244px;border-radius:50%;background:var(--white);z-index:4;}
.brand{position:absolute;left:138px;top:78px;width:244px;text-align:center;z-index:5;font-family:"Montserrat",sans-serif;font-weight:700;color:var(--blue);font-size:17px;line-height:1.15;}
.brand-dot{display:block;width:44px;height:44px;border-radius:50%;border:3px solid var(--blue);margin:-62px auto 18px;}
.nav{position:absolute;right:145px;top:30px;display:flex;gap:44px;z-index:5;font-family:"Montserrat",sans-serif;font-weight:700;font-size:14px;}
.nav a{color:var(--ink);text-decoration:none;}
.nav a.active{color:var(--blue);}
.hero-title{position:absolute;top:190px;left:0;width:1200px;text-align:center;font-family:"Montserrat",sans-serif;font-weight:800;font-size:45px;line-height:51px;color:var(--white);text-transform:uppercase;letter-spacing:-1px;margin:0;text-shadow:0 2px 6px rgba(0,0,0,.5);}
.dots{position:absolute;top:554px;left:571px;display:flex;gap:14px;}
.dots span{width:10px;height:10px;border-radius:50%;background:var(--white);}
.dots span.on{background:var(--blue);}
.seal{position:absolute;width:52px;height:52px;border-radius:50%;background:var(--white);border:3px solid #ddd;box-sizing:border-box;}
.seal::after{content:"";position:absolute;inset:10px;border-radius:50%;background:var(--blue);opacity:.7;}
/* about */
.faint-ring{position:absolute;border-radius:50%;border:10px solid #eee;box-sizing:border-box;}
.portrait{position:absolute;left:167px;top:733px;width:388px;height:388px;border-radius:50%;background:radial-gradient(circle at 50% 40%,#b89a86 0,#7a5a48 35%,#3a2b24 60%,#ececec 61%,#f3f3f3 100%);}
.about-text{position:absolute;left:600px;top:810px;width:456px;font-size:12.6px;line-height:21.7px;color:var(--text);text-align:justify;margin:0;}
/* services */
.service{position:absolute;width:240px;}
.service h3{margin:0 0 14px;font-family:"Montserrat",sans-serif;font-weight:700;font-size:15px;line-height:20px;color:var(--ink);text-transform:uppercase;}
.service p{margin:0;font-size:11px;line-height:19px;color:var(--muted);}
.service.left{text-align:right;}
.icon-dot{position:absolute;width:66px;height:66px;border-radius:50%;display:flex;align-items:center;justify-content:center;}
/* media */
.media{position:absolute;top:1757px;height:373px;}
.play{position:absolute;left:780px;top:1920px;width:46px;height:46px;border-radius:50%;background:var(--red);}
.play::after{content:"";position:absolute;left:18px;top:13px;border-left:15px solid var(--white);border-top:10px solid transparent;border-bottom:10px solid transparent;}
/* insights */
.card{position:absolute;background:var(--white);border:1px solid #ececec;box-sizing:border-box;}
.card.featured{border:2px solid var(--blue);}
.thumb{position:absolute;}
.meta{font-family:"Montserrat",sans-serif;font-weight:700;font-size:13px;color:var(--red);margin:0;}
.card-title{font-family:"Montserrat",sans-serif;font-weight:700;font-size:18px;line-height:24px;color:var(--ink);margin:0;}
.card-text{font-size:12px;line-height:22px;color:var(--muted);margin:0;}
.read-more{font-family:"Montserrat",sans-serif;font-weight:700;font-size:15px;color:var(--blue);text-transform:uppercase;}
/* contact */
.field{position:absolute;background:var(--white);font-size:15px;color:#555;padding:0 21px;box-sizing:border-box;display:flex;align-items:center;}
.field.area{align-items:flex-start;padding-top:20px;}
.footer-note{position:absolute;left:145px;top:3621px;font-size:13px;color:#333;}
.socials{position:absolute;left:902px;top:3619px;display:flex;gap:7px;}
.socials span{width:24px;height:24px;border-radius:50%;border:1.5px solid var(--blue);box-sizing:border-box;}
</style>
</head>
<body>
<div class="page">

  <!-- header -->
  <header class="site-header">
    <div class="top-stripes"><span style="background:var(--blue)"></span><span style="background:var(--green)"></span><span style="background:var(--orange)"></span><span style="background:var(--red)"></span></div>
    <nav class="nav">
      <a class="active" href="#">HOME</a><a href="#">ABOUT US</a><a href="#">INSIGHTS</a><a href="#">SERVICES</a><a href="#">CONTACT US</a>
    </nav>
  </header>
  <div class="brand-badge"></div>
  <div class="brand"><span class="brand-dot"></span>CORINNE HABBARD</div>

  <!-- hero -->
  <svg class="abs" style="left:0;top:0" width="1200" height="700" viewBox="0 0 1200 700">
    <defs>
      <linearGradient id="heroTone" x1="0" y1="0" x2="1" y2="1">
        <stop offset="0" stop-color="#5a4a44"/><stop offset=".5" stop-color="#2b2a30"/><stop offset="1" stop-color="#3a4358"/>
      </linearGradient>
    </defs>
    <path d="M0 76 H1200 V448 Q600 868 0 448 Z" fill="url(#heroTone)" role="img" aria-label="Photo of a seated panel discussion in front of an audience"/>
    <path d="M0 452 Q600 876 1200 452" fill="none" stroke="#111" stroke-width="6"/>
  </svg>
  <h1 class="hero-title">Clinical Information<br>Analyst Staff Specialist<br>at Lakeshore Health</h1>
  <div class="btn" style="left:535px;top:370px;width:132px;height:44px;">Get Started</div>
  <div class="dots"><span></span><span class="on"></span><span></span></div>
  <div class="seal" style="left:574px;top:626px;"></div>

  <!-- about -->
  <div class="faint-ring" style="left:95px;top:1040px;width:216px;height:216px;"></div>
  <div class="faint-ring" style="left:968px;top:1036px;width:216px;height:216px;"></div>
  <svg class="abs" style="left:140px;top:705px" width="440" height="440" viewBox="0 0 440 440">
    <path d="M220 8 A212 212 0 1 0 360 378" fill="none" stroke="#111" stroke-width="5"/>
    <path d="M220 12 A208 208 0 0 1 425 220" fill="none" stroke="#111" stroke-width="3"/>
  </svg>
  <div class="portrait" role="img" aria-label="Portrait photo of Corinne Habbard"></div>
  <h2 class="heading abs" style="left:600px;top:742px;">ABOUT ME</h2>
  <p class="about-text">The National Leadership Fellows Class of 2024 met in Little Rock, AR for module 2 last week. We learned leadership skills focused on vision and communication. We heard from many distinguished speakers including Former President Walter Hale, Former Secretary Raymond Ortega, Former Secretary Martin Blake, Former Press Secretary Janet Moore, Congressman Gordon Pike, and Harbor Foundation CEO Neil Carver. It was amazing to hear about their experiences.I was also able to spend time with my amazing cohort and learn about the exciting work they are doing across the country as leaders. I can't wait to go to College Station, TX next month to continue our journey.</p>
  <div class="btn" style="left:600px;top:1052px;width:120px;height:44px;">Read More</div>

  <!-- services -->
  <svg class="abs" style="left:0;top:1150px" width="1200" height="260" viewBox="0 1150 1200 260">
    <path d="M0 1390 Q600 965 1200 1390" fill="none" stroke="#111" stroke-width="3"/>
  </svg>
  <h2 class="heading abs" style="left:0;width:1200px;text-align:center;top:1268px;">SERVICES</h2>

  <div class="service left" style="left:170px;top:1385px;"><h3>Nemo enim ipsam vo<br>luptatem quia</h3><p>Lorem ipsum dolor sit amet, consectetur adipiscing elit sed do eiusmod tempor</p></div>
  <div class="service left" style="left:170px;top:1592px;"><h3>Nemo enim ipsam volupt<br>atem quia voluptas</h3><p>Lorem ipsum dolor sit amet, consectetur adipiscing elit, sed do eiusmod</p></div>
  <div class="service" style="left:789px;top:1385px;"><h3>Duis aute irure dolor<br>in repre</h3><p>Lorem ipsum dolor sit amet, consectetur adipiscing elit, sed do eiusmod tempor incididunt ut labore et dolore magna aliqua.</p></div>
  <div class="service" style="left:789px;top:1592px;"><h3>Neque porro quisquam est</h3><p style="margin-top:-2px">Lorem ipsum dolor sit amet, consectetur adipiscing elit, sed do eiusmod tempor incididunt ut labore et dolore magna aliqua.</p></div>

  <svg class="abs" style="left:447px;top:1390px" width="300" height="300" viewBox="0 0 300 300">
    <circle cx="150" cy="150" r="143" fill="none" stroke="#111" stroke-width="6" stroke-dasharray="150 75" stroke-dashoffset="-35"/>
    <circle cx="150" cy="150" r="112" fill="none" stroke="#e2e2e2" stroke-width="2"/>
    <circle cx="150" cy="150" r="80" fill="#fff" stroke="#111" stroke-width="3"/>
    <circle cx="150" cy="150" r="72" fill="none" stroke="#ddd" stroke-width="1"/>
  </svg>
  <div class="icon-dot" style="left:447px;top:1397px;background:var(--blue);"><svg width="30" height="30" viewBox="0 0 30 30" fill="none" stroke="#fff" stroke-width="2"><circle cx="15" cy="9" r="5"/><path d="M5 27c0-6 4-10 10-10s10 4 10 10"/></svg></div>
  <div class="icon-dot" style="left:687px;top:1397px;background:var(--green);"><svg width="30" height="30" viewBox="0 0 30 30" fill="none" stroke="#fff" stroke-width="2"><circle cx="15" cy="11" r="6"/><path d="M3 24h8l4 3 12-5"/></svg></div>
  <div class="icon-dot" style="left:447px;top:1607px;background:var(--red);"><svg width="30" height="30" viewBox="0 0 30 30" fill="none" stroke="#fff" stroke-width="2"><rect x="7" y="3" width="16" height="10"/><circle cx="15" cy="18" r="3"/><path d="M8 28c0-4 3-6 7-6s7 2 7 6"/></svg></div>
  <div class="icon-dot" style="left:687px;top:1607px;background:var(--orange);"><svg width="30" height="30" viewBox="0 0 30 30" fill="none" stroke="#fff" stroke-width="2"><path d="M5 15a10 10 0 0 1 20 0v5h-4v-6h4M5 14h4v6H5z"/></svg></div>

  <!-- media -->
  <div class="media" style="left:0;width:394px;background:linear-gradient(135deg,#c9c1b4,#7d8590 55%,#3e3a38);" role="img" aria-label="Photo of an audience watching a panel in a glass-walled hall"></div>
  <div class="media" style="left:400px;width:800px;background:linear-gradient(90deg,#2c3b7a,#3a4c93 50%,#2a3a78);" role="img" aria-label="Video still of two speakers in conversation on stage"></div>
  <div class="play"></div>

  <!-- insights -->
  <div class="faint-ring" style="left:1050px;top:2125px;width:216px;height:216px;"></div>
  <h2 class="heading abs" style="left:0;width:1200px;text-align:center;top:2208px;">LATEST INSIGHTS</h2>

  <div class="card" style="left:133px;top:2305px;width:296px;height:502px;">
    <div class="thumb" style="left:2px;top:1px;width:292px;height:209px;background:linear-gradient(180deg,#b9c3cc,#6a6f78 55%,#3c3a3c);" role="img" aria-label="Group photo of the leadership fellows cohort outdoors"></div>
    <div class="abs" style="left:21px;top:238px;width:250px;">
      <p class="meta">April 22,2024 &nbsp;|&nbsp; John Doe</p>
      <p class="card-title" style="margin-top:16px;">Sed ut perspiciatis unde omnis iste natus</p>
      <p class="card-text" style="margin-top:18px;">Ut enim ad minima veniam, quis nostreierci tationem ullam corporis suscipit laboriosam isi ut aliquid ex ea commodi eprehenderitq ui in ea</p>
      <p class="read-more" style="margin-top:32px;">Read More</p>
    </div>
  </div>

  <div class="card featured" style="left:446px;top:2301px;width:609px;height:245px;">
    <div class="thumb" style="left:8px;top:9px;width:220px;height:224px;background:linear-gradient(180deg,#e9e4da,#c7b9a3 45%,#6b3a2c);" role="img" aria-label="Photo of a nurse standing in a formal government room"></div>
    <div class="abs" style="left:270px;top:22px;width:310px;">
      <p class="meta">April 22,2024 &nbsp;|&nbsp; John Doe</p>
      <p class="card-title" style="margin-top:14px;">A longtime Lakeshore Health nurse is now a National Leadership Fellow</p>
      <p class="card-text" style="margin-top:12px;">Lakeshore Health nurse Corinne Habbard in the Capitol as part of the National</p>
      <p class="read-more" style="margin-top:14px;">Read More</p>
    </div>
  </div>

  <div class="card" style="left:446px;top:2560px;width:609px;height:246px;">
    <div class="thumb" style="left:2px;top:1px;width:237px;height:242px;background:linear-gradient(135deg,#3b4f8f,#b08a7a 55%,#2c2f3c);" role="img" aria-label="Photo of two speakers seated on stage"></div>
    <div class="abs" style="left:270px;top:30px;width:310px;">
      <p class="meta">April 22,2024 &nbsp;|&nbsp; John Doe</p>
      <p class="card-title" style="margin-top:14px;">Sed ut perspiciatis unde omnis iste natus error</p>
      <p class="card-text" style="margin-top:12px;">Ut enim ad minima veniam, quis nostreierci tationem ullam corporis suscipit laboriosam isi ut aliquid ex ea eprehenderitq utate velit .</p>
      <p class="read-more" style="margin-top:14px;">Read More</p>
    </div>
  </div>

  <div class="btn" style="left:496px;top:2842px;width:208px;height:46px;">View More Insights</div>

  <!-- contact -->
  <div class="faint-ring" style="left:20px;top:2820px;width:216px;height:216px;"></div>
  <svg class="abs" style="left:0;top:2780px" width="1200" height="860" viewBox="0 2780 1200 860">
    <defs>
      <linearGradient id="contactTone" x1="0" y1="0" x2="0" y2="1">
        <stop offset="0" stop-color="#1a8fd6"/><stop offset="1" stop-color="#1c87cc"/>
      </linearGradient>
    </defs>
    <path d="M0 3130 Q600 2790 1200 3130 V3440 Q600 3730 0 3440 Z" fill="url(#contactTone)" role="img" aria-label="Blue-toned crowd photo behind the contact form"/>
    <path d="M0 3134 Q600 2794 1200 3134" fill="none" stroke="#111" stroke-width="3"/>
    <path d="M0 3446 Q600 3744 1200 3446" fill="none" stroke="#111" stroke-width="5"/>
  </svg>
  <div class="seal" style="left:574px;top:2932px;"></div>
  <h2 class="heading abs" style="left:0;width:1200px;text-align:center;top:3050px;color:var(--white);">CONTACT US</h2>
  <div class="field" style="left:235px;top:3150px;width:360px;height:53px;">First Name</div>
  <div class="field" style="left:607px;top:3150px;width:360px;height:53px;">Last Name</div>
  <div class="field" style="left:235px;top:3215px;width:360px;height:53px;">Email address</div>
  <div class="field" style="left:607px;top:3215px;width:360px;height:53px;">Phone Number</div>
  <div class="field area" style="left:235px;top:3280px;width:732px;height:115px;">Message</div>
  <div class="btn" style="left:496px;top:3440px;width:208px;height:45px;">Submit Message</div>

  <!-- footer -->
  <div class="footer-note">© 2024 Corinne Habbard. All rights reserved.Privacy &nbsp;|&nbsp; Terms of Use</div>
  <div class="socials" aria-label="Social links"><span></span><span></span><span></span><span></span><span></span></div>

</div>
</body>
</html>
```